Awesome business card design needed

We need a new business card design to go with our new logo.
We are a web development agency that specialises in highly complex back-end integrations as opposed to design, our customers are retailers, hotels, hospitals and any other organisation that has a large online marketing department.
Take a look at our website - www.brenoloft.com for some inspiration.
We want our new business cards to exude class, professionalism and style.
We are likely to choose a high-end card to print them on but we want the design of the card itself to really turn heads.
We have no specific colour requirements, the logo as you will see is a turquoise colour R89 G171 B167 #59aba7 but it can also be in white if you want to make the colour of the card something different.
The information on the card should be:
Name
Position
Tel
email
Potentially a double sided card could have our web address, twitter and FB links.

```html
<!DOCTYPE html>
<html lang="en">
<head>
<meta charset="utf-8">
<title>Brenoloft Business Card</title>
<link rel="stylesheet" href="https://fonts.googleapis.com/css2?family=Michroma&family=Open+Sans:wght@400;700&display=swap">
<style>
  :root {
    --turquoise: #59aba7;
    --charcoal: #3a3a3a;
    --ink: #333333;
    --muted: #555555;
    --rule: #d6d6d6;
    --paper: #ffffff;
    --backdrop: #eceae6;
  }
  * { box-sizing: border-box; margin: 0; padding: 0; }
  html, body { width: 1200px; height: 720px; overflow: hidden; }
  body {
    background: var(--backdrop);
    position: relative;
    font-family: "Open Sans", Arial, sans-serif;
  }
  .card {
    position: absolute;
    width: 520px;
    height: 297px;
    background: var(--paper);
    overflow: hidden;
    box-shadow: 0 6px 18px rgba(0,0,0,0.12);
  }
  .card--front { left: 50px; top: 212px; }
  .card--back  { left: 630px; top: 212px; }

  /* Front */
  .brand-name {
    font-family: "Michroma", Arial, sans-serif;
    color: var(--turquoise);
    font-weight: 400;
    letter-spacing: 1px;
  }
  .card--front .brand-name {
    position: absolute;
    left: 34px;
    top: 128px;
    font-size: 30px;
  }
  .divider {
    position: absolute;
    left: 330px;
    top: 26px;
    width: 1px;
    height: 84px;
    background: var(--rule);
  }
  .contact {
    position: absolute;
    left: 346px;
    top: 26px;
    font-size: 12.5px;
    color: var(--muted);
    line-height: 1.5;
  }
  .contact__name { font-weight: 700; font-size: 16px; color: var(--ink); line-height: 1.2; }
  .contact__role { color: var(--turquoise); font-size: 12px; margin-bottom: 6px; }
  .contact__line { display: flex; align-items: center; gap: 6px; }
  .contact__line svg { width: 11px; height: 11px; flex: none; }
  .card__bands { position: absolute; left: 0; top: 0; width: 520px; height: 297px; }
  .web-address {
    position: absolute;
    right: 18px;
    top: 219px;
    font-family: "Michroma", Arial, sans-serif;
    font-size: 11px;
    color: var(--paper);
    letter-spacing: 1px;
  }
  .street-address {
    position: absolute;
    left: 28px;
    bottom: 12px;
    font-family: "Michroma", Arial, sans-serif;
    font-size: 10.5px;
    color: var(--ink);
    letter-spacing: 0.5px;
  }

  /* Back */
  .card--back .brand-name {
    position: absolute;
    left: 0; right: 0;
    top: 96px;
    text-align: center;
    font-size: 38px;
  }
  .follow {
    position: absolute;
    left: 0; right: 0;
    top: 178px;
    display: flex;
    justify-content: center;
    align-items: center;
    gap: 8px;
    font-weight: 700;
    font-size: 15px;
    color: var(--turquoise);
    letter-spacing: 0.5px;
  }
  .social-mark {
    width: 26px; height: 26px;
    border-radius: 4px;
    background: var(--turquoise);
  }
  .back-web {
    position: absolute;
    left: 0; right: 0;
    top: 216px;
    text-align: center;
    font-family: "Michroma", Arial, sans-serif;
    font-size: 13px;
    color: var(--ink);
    letter-spacing: 1.5px;
  }
  .back-web strong { color: var(--turquoise); font-weight: 400; }
</style>
</head>
<body>

  <section class="card card--front" aria-label="Business card front">
    <svg class="card__bands" viewBox="0 0 520 297" aria-hidden="true">
      <path d="M0 262 C150 254 300 246 350 224 Q370 214 400 212 L520 212 L520 236 L0 270 Z" fill="#59aba7"/>
      <path d="M0 270 L520 236 L520 240 L0 274 Z" fill="#3a3a3a"/>
    </svg>
    <div class="brand-name">brenoloft</div>
    <div class="divider"></div>
    <div class="contact">
      <div class="contact__name">Your Name</div>
      <div class="contact__role">Position</div>
      <div class="contact__line">
        <svg viewBox="0 0 12 12"><path d="M3 1 L5 3.5 L4 5 Q5 7 7 8 L8.5 7 L11 9 L10 11 Q5 11 1 2 Z" fill="#59aba7"/></svg>
        <span>123-456-7890</span>
      </div>
      <div class="contact__line">
        <svg viewBox="0 0 12 12"><rect x="1" y="3" width="10" height="7" rx="1" fill="#59aba7"/><path d="M1.5 3.5 L6 7 L10.5 3.5" stroke="#fff" fill="none" stroke-width="1"/></svg>
        <span>info@brenoloft.com</span>
      </div>
    </div>
    <div class="web-address">www.brenoloft.com</div>
    <div class="street-address">Street Name, City Name, State Zip Code</div>
  </section>

  <section class="card card--back" aria-label="Business card back">
    <div class="brand-name">brenoloft</div>
    <div class="follow">
      <span>Follow Us On:</span>
      <span class="social-mark"></span>
      <span class="social-mark"></span>
    </div>
    <div class="back-web">www.<strong>brenoloft</strong>.com</div>
  </section>

</body>
</html>
```